Landing Page / Waitlist

I would like a landing page for people to sign up for a waiting list. The text on the page should include (but is not limited to):
1) Main point: The accounting system you'll love
2) Secondary points:
a. Ruthlessly efficient
b. Quietly intelligent
c. Driven by AI
I've attached a file of our logo

The design should be simple, clean, and innovative - this is an ai company

```html
<!DOCTYPE html>
<html lang="en">
<head>
<meta charset="utf-8">
<title>ClearTally – Join the Waitlist</title>
<link rel="stylesheet" href="https://fonts.googleapis.com/css2?family=Poppins:wght@300;400;500;600;800&display=swap">
<style>
  :root {
    --brand-blue: #0b8bff;
    --brand-blue-dark: #0a6fe0;
    --ink-grey: #6b6b6b;
    --ink-soft: #7a7a7a;
    --ink-dark: #2a2a2a;
    --card-border: #d4d4d4;
    --page-bg: #ffffff;
    --foot-tint: #cfe6fb;
  }
  * { box-sizing: border-box; margin: 0; padding: 0; }
  html, body { width: 1200px; height: 746px; overflow: hidden; }
  body {
    position: relative;
    font-family: "Poppins", sans-serif;
    background: linear-gradient(180deg, var(--page-bg) 0%, var(--page-bg) 84%, var(--foot-tint) 100%);
    color: var(--ink-grey);
  }
  .brand {
    position: absolute; left: 75px; width: 616px; top: 128px;
    text-align: center;
    font-weight: 600; font-size: 44px; letter-spacing: -1px;
    color: var(--ink-grey);
  }
  .headline {
    position: absolute; left: 40px; width: 700px; top: 221px;
    text-align: center; white-space: nowrap;
    font-size: 68px; line-height: 75px; font-weight: 300;
    color: var(--ink-grey); letter-spacing: -1px;
  }
  .headline strong { font-weight: 800; color: var(--brand-blue); }
  .features { position: absolute; left: 75px; top: 427px; display: flex; gap: 14px; }
  .feature {
    width: 195px; height: 123px;
    border: 1px solid var(--card-border); border-radius: 9px;
    display: flex; flex-direction: column; align-items: center; justify-content: center; gap: 12px;
  }
  .feature svg { width: 40px; height: 40px; }
  .feature span { font-size: 14.5px; font-weight: 500; color: var(--ink-soft); }
  .signup {
    position: absolute; left: 75px; top: 590px; width: 616px; height: 51px;
    border: 1px solid #8a8a8a; border-radius: 13px;
    display: flex; align-items: center; padding: 0 4px 0 20px;
  }
  .signup svg { width: 16px; height: 12px; margin-right: 12px; }
  .signup input {
    flex: 1; border: none; outline: none; background: transparent;
    font-family: "Poppins", sans-serif; font-size: 14px; color: var(--ink-soft);
  }
  .signup input::placeholder { color: var(--ink-soft); }
  .signup button {
    width: 171px; height: 41px; border: none; border-radius: 12px;
    background: var(--brand-blue); color: #fff;
    font-family: "Poppins", sans-serif; font-weight: 600; font-size: 17px;
  }
  .hero-art {
    position: absolute; left: 769px; top: 90px; width: 341px; height: 532px;
    border-radius: 40px;
    background: radial-gradient(ellipse at 50% 22%, #2e5fa8 0%, #3b78b8 22%, #dfe8ea 40%, #eef3f3 70%, rgba(255,255,255,0) 100%);
  }
  .copyright {
    position: absolute; left: 0; width: 1200px; top: 694px;
    text-align: center; font-size: 12px; color: var(--ink-dark);
  }
</style>
</head>
<body>
  <div class="brand">ClearTally</div>

  <h1 class="headline">The <strong>accounting</strong><br><strong>system</strong> you'll love</h1>

  <section class="features">
    <div class="feature">
      <svg viewBox="0 0 40 40" fill="none" stroke="var(--brand-blue)" stroke-width="1.6">
        <circle cx="20" cy="20" r="13"/>
        <path d="M20 4v4M20 32v4M4 20h4M32 20h4M8.7 8.7l2.8 2.8M28.5 28.5l2.8 2.8M8.7 31.3l2.8-2.8M28.5 11.5l2.8-2.8"/>
        <path d="M11 25l6-6 4 4 8-9M25 14h4v4"/>
      </svg>
      <span>Ruthlessly efficient</span>
    </div>
    <div class="feature">
      <svg viewBox="0 0 40 40" fill="none" stroke="var(--brand-blue)" stroke-width="1.6">
        <circle cx="20" cy="20" r="7"/>
        <text x="20" y="23" text-anchor="middle" font-size="7" font-family="Poppins, sans-serif" fill="var(--brand-blue)" stroke="none">AI</text>
        <path d="M20 13V6M20 27v7M13 20H6M27 20h7M15 15l-5-5M25 25l5 5M15 25l-5 5M25 15l5-5"/>
        <circle cx="20" cy="4" r="2"/><circle cx="20" cy="36" r="2"/><circle cx="4" cy="20" r="2"/><circle cx="36" cy="20" r="2"/>
        <circle cx="8.5" cy="8.5" r="2"/><circle cx="31.5" cy="31.5" r="2"/><circle cx="8.5" cy="31.5" r="2"/><circle cx="31.5" cy="8.5" r="2"/>
      </svg>
      <span>Quietly intelligent</span>
    </div>
    <div class="feature">
      <svg viewBox="0 0 40 40" fill="none" stroke="var(--brand-blue)" stroke-width="2" stroke-linejoin="round">
        <path d="M15 10c1 6 3 8 9 9-6 1-8 3-9 9-1-6-3-8-9-9 6-1 8-3 9-9z"/>
        <path d="M30 4c.5 3 1.5 4 4 4.5-2.5.5-3.5 1.5-4 4.5-.5-3-1.5-4-4-4.5 2.5-.5 3.5-1.5 4-4.5z"/>
        <path d="M30 26c.5 3 1.5 4 4 4.5-2.5.5-3.5 1.5-4 4.5-.5-3-1.5-4-4-4.5 2.5-.5 3.5-1.5 4-4.5z"/>
      </svg>
      <span>Driven by AI</span>
    </div>
  </section>

  <form class="signup">
    <svg viewBox="0 0 16 12" fill="none" stroke="var(--ink-soft)" stroke-width="1.1">
      <rect x="0.6" y="0.6" width="14.8" height="10.8" rx="1.5"/>
      <path d="M1 1.5l7 5 7-5"/>
    </svg>
    <input type="email" placeholder="Email id" aria-label="Email address">
    <button type="button">Join the Waitlist</button>
  </form>

  <div class="hero-art" role="img" aria-label="Isometric illustration of an AI chip module mounted above a white gear, connected by glowing teal wires"></div>

  <p class="copyright">Copyright © 2025 All Rights Reserved</p>
</body>
</html>
```